New iOS App design for Boston Startup

We are looking for a new app design for our iPhone app. The current app's design feels outdated and we like to add lots of new functionality and a new navigation as well. A complete overhaul therefore!
We want you to design 5 screens that will have changed the most. The complete wireframes of these 5 pages are attached in the requirements document.
Once the winning design is selected we will award the winner with the designing all other screens (40-50 screens based on the same design). This will be a separate project worth $1000. The winning designer can get more follow up work if both sides are happy about the cooperation.
We will give feedback as soon as the first screen has been uploaded for review. Final decision will be made only after all 5 screens are finished.
We hope you give it your best!
Note: will only communicate through PixelHarbor (no skype),
Updates
Reason: Want to give designers a chance to submit their designs as I understand from some, the deadline is too close.
I have raised the award and introduced a 2nd price as well to make it worth your time. I hope you give it your best shot.
Reason: A few of you have asked for an extension of the deadline as time is running out. I will extend by one day. Tell me if you need more.
Industry/Entity Type
Startup
Requirements
Must have
- At least 1 screen before we can give you feedback.
Nice to have
- multiple options of 1 screen to get to a desirable design

```html
<!DOCTYPE html>
<html lang="en">
<head>
<meta charset="utf-8">
<title>Study App – Home Screen Variants</title>
<link rel="stylesheet" href="https://fonts.googleapis.com/css2?family=Lato:wght@300;400;700&display=swap">
<style>
  :root {
    --canvas-bg: #b3babd;
    --brand-blue: #1aabd6;
    --text-dark: #555a5e;
    --text-muted: #9a9ea1;
    --line-light: #cfd3d5;
    --up-green: #2fcf4a;
    --down-red: #ef4136;
    --light-bg: #ffffff;
    --blue-bg: #eaf4fb;
    --dark-bg: #1e1f20;
    --dark-band: #303132;
    --dark-bar: #232425;
    --white: #ffffff;
  }
  * { box-sizing: border-box; margin: 0; padding: 0; }
  html, body { width: 1200px; height: 1000px; overflow: hidden; }
  body {
    background: var(--canvas-bg);
    font-family: "Lato", "Helvetica Neue", Arial, sans-serif;
    position: relative;
  }
  .icon-defs { position: absolute; width: 0; height: 0; }

  .screen {
    position: absolute;
    width: 380px;
    height: 565px;
    overflow: hidden;
    --fg: var(--text-dark);
    --muted: var(--text-muted);
    --rule: var(--line-light);
  }
  .screen > * { position: absolute; }

  .screen--light { left: 18px; top: 230px; background: var(--light-bg); }
  .screen--blue  { left: 414px; top: 195px; background: var(--blue-bg); }
  .screen--dark  { left: 806px; top: 160px; background: var(--dark-bg);
    --fg: #c9cbcc; --muted: #8d9092; --rule: #55585a; }

  /* app bar */
  .app-bar { left: 0; top: 0; width: 100%; height: 60px; border-bottom: 1px solid var(--rule); }
  .app-bar h1 { text-align: center; font-weight: 300; font-size: 32px; line-height: 60px; color: var(--fg); letter-spacing: -0.5px; }
  .menu-icon { position: absolute; left: 24px; top: 20px; width: 24px; height: 20px; color: var(--fg); }
  .screen--light .app-bar h1 { color: #6d7173; }
  .screen--blue .app-bar { background: var(--brand-blue); border: 0; }
  .screen--blue .app-bar h1, .screen--blue .menu-icon { color: var(--white); }
  .screen--dark .app-bar { background: #18191a; border: 0; height: 64px; }
  .screen--dark .app-bar h1 { color: var(--white); line-height: 64px; }
  .screen--dark .menu-icon { color: var(--white); }

  /* greeting */
  .greeting { color: var(--brand-blue); }
  .greeting__hello { font-size: 15px; font-weight: 400; }
  .greeting__name { font-size: 38px; font-weight: 400; line-height: 1; margin-top: 2px; letter-spacing: 0.5px; }
  .screen--light .greeting { left: 0; top: 60px; width: 195px; height: 65px; padding: 6px 0 0 22px; border-right: 1px solid var(--rule); border-bottom: 1px solid var(--rule); }
  .screen--light .greeting-rule { left: 195px; top: 124px; width: 185px; height: 1px; background: var(--rule); }
  .screen--blue .greeting { left: 14px; top: 66px; width: 352px; height: 58px; background: var(--white); text-align: center; padding-top: 4px; }
  .screen--blue .greeting__name { font-size: 36px; }
  .screen--dark .greeting-band { left: 0; top: 66px; width: 100%; height: 66px; background: var(--dark-band); }
  .screen--dark .greeting { left: 20px; top: 72px; }
  .screen--dark .greeting__name { font-size: 36px; }

  /* score */
  .score { color: var(--fg); }
  .score__label { display: block; font-size: 11px; letter-spacing: 0.3px; }
  .score__row { display: flex; align-items: center; gap: 6px; }
  .score__value { font-size: 38px; font-weight: 300; line-height: 1; }
  .score__arrow { width: 16px; height: 22px; color: var(--down-red); }
  .score__delta { font-size: 24px; font-weight: 300; margin-left: 6px; margin-top: 6px; }
  .screen--light .score { left: 210px; top: 68px; }
  .screen--blue .score { left: 0; top: 126px; width: 100%; text-align: center; }
  .screen--blue .score__row { justify-content: center; margin-left: 50px; }
  .screen--dark .score { left: 226px; top: 74px; color: var(--white); }
  .screen--dark .score__label { color: #d7d9da; }

  /* period tabs */
  .period-tabs { left: 14px; width: 352px; height: 30px; display: flex; font-size: 15px; color: var(--muted); }
  .period-tabs span { flex: 1; text-align: center; line-height: 28px; }
  .period-tabs .is-active { color: var(--brand-blue); border: 1.5px solid var(--brand-blue); border-bottom: 0; }
  .period-tabs span:not(.is-active) { border-bottom: 1.5px solid var(--rule); }
  .screen--light .period-tabs { top: 142px; }
  .screen--blue .period-tabs { top: 182px; }
  .screen--dark .period-tabs { top: 152px; }
  .screen--dark .period-tabs span:not(.is-active) { color: #9a9d9f; }

  /* stats carousel */
  .stats { left: 10px; width: 360px; height: 48px; }
  .stats__chevron { position: absolute; top: 12px; width: 14px; height: 22px; color: var(--brand-blue); }
  .stats__chevron--prev { left: 0; }
  .stats__chevron--next { right: 0; }
  .stats__track { position: absolute; left: 24px; top: 0; width: 312px; height: 48px; overflow: hidden; border-right: 1px solid var(--rule); }
  .stat { position: absolute; top: 0; }
  .stat__label { display: block; font-size: 15px; font-weight: 700; color: var(--brand-blue); }
  .stat__value { display: flex; align-items: center; font-size: 20px; font-weight: 700; color: var(--fg); margin-top: 1px; white-space: nowrap; }
  .stat__up { width: 10px; height: 14px; color: var(--up-green); margin: 0 2px 0 3px; }
  .stat:nth-child(1) { left: -4px; }
  .stat:nth-child(1) .stat__value { margin-left: -10px; }
  .stat:nth-child(2) { left: 128px; }
  .stat:nth-child(3) { left: 234px; }
  .screen--light .stats { top: 174px; }
  .screen--blue .stats { top: 212px; }
  .screen--dark .stats { top: 182px; }

  .section-rule { left: 14px; width: 352px; height: 1px; background: var(--rule); }
  .screen--light .section-rule { top: 229px; }
  .screen--blue .section-rule { top: 268px; }
  .screen--dark .section-rule { top: 237px; background: #8a8d8f; }

  /* shortcuts */
  .shortcuts { left: 0; width: 100%; list-style: none; display: flex; justify-content: center; gap: 2px; }
  .shortcut { width: 94px; text-align: center; font-size: 10px; color: var(--muted); }
  .shortcut__circle { width: 54px; height: 54px; margin: 0 auto 7px; border-radius: 50%; border: 1.5px solid #bfc3c5; display: flex; align-items: center; justify-content: center; color: #9ea2a4; font-size: 20px; font-weight: 300; }
  .shortcut__circle svg { width: 30px; height: 30px; }
  .shortcut--active .shortcut__circle { background: var(--brand-blue); border-color: var(--brand-blue); color: var(--white); }
  .screen--light .shortcuts { top: 246px; left: -6px; }
  .screen--blue .shortcuts { top: 284px; }
  .screen--dark .shortcuts { top: 250px; left: -8px; }
  .screen--dark .shortcut { color: #e3e4e5; font-size: 10.5px; }
  .screen--dark .shortcut__circle { border-color: #e3e4e5; color: #e3e4e5; }

  /* up next */
  .up-next { left: 0; width: 100%; text-align: center; font-size: 19px; font-weight: 300; color: #6c7073; line-height: 25px; }
  .up-next__label { margin-right: 8px; }
  .screen--light .up-next { top: 366px; }
  .screen--blue .up-next { top: 393px; }
  .screen--dark .up-next { top: 372px; color: #7e8183; }

  /* tab bar */
  .tab-bar { left: 0; top: 500px; width: 100%; height: 65px; display: flex; border-top: 1px solid var(--rule); background: var(--light-bg); }
  .tab-bar__item { flex: 1; display: flex; flex-direction: column; align-items: center; padding-top: 10px; font-size: 10.5px; color: #6e7275; position: relative; }
  .tab-bar__item svg { width: 34px; height: 32px; margin-bottom: 4px; color: #6e7275; }
  .tab-bar__item.is-active { color: var(--brand-blue); }
  .tab-bar__item.is-active svg { color: var(--brand-blue); }
  .tab-bar__item.is-active::before { content: ""; position: absolute; top: -2px; left: 0; right: 0; height: 3px; background: var(--brand-blue); }
  .screen--blue .tab-bar { top: 500px; }
  .screen--dark .tab-bar { background: var(--dark-bar); border-top-color: #3a3c3d; }
  .screen--dark .tab-bar__item, .screen--dark .tab-bar__item svg { color: #8b8e90; }
  .screen--dark .tab-bar__item.is-active, .screen--dark .tab-bar__item.is-active svg { color: var(--brand-blue); }
</style>
</head>
<body>

<svg class="icon-defs" aria-hidden="true">
  <defs>
    <symbol id="i-menu" viewBox="0 0 24 20"><rect y="0" width="24" height="3.4" fill="currentColor"/><rect y="8.3" width="24" height="3.4" fill="currentColor"/><rect y="16.6" width="24" height="3.4" fill="currentColor"/></symbol>
    <symbol id="i-down" viewBox="0 0 16 22"><path d="M5 0h6v12h5L8 22 0 12h5z" fill="currentColor"/></symbol>
    <symbol id="i-up" viewBox="0 0 10 14"><path d="M3.5 14V6H0L5 0l5 6H6.5v8z" fill="currentColor"/></symbol>
    <symbol id="i-prev" viewBox="0 0 14 22"><path d="M11 2 3 11l8 9" fill="none" stroke="currentColor" stroke-width="3.5"/></symbol>
    <symbol id="i-next" viewBox="0 0 14 22"><path d="M3 2l8 9-8 9" fill="none" stroke="currentColor" stroke-width="3.5"/></symbol>
    <symbol id="i-chart" viewBox="0 0 30 30" fill="none" stroke="currentColor" stroke-width="1.6"><rect x="6" y="11" width="5" height="12"/><rect x="12.5" y="6" width="5" height="17"/><rect x="19" y="13" width="5" height="10"/><path d="M4 24h22"/></symbol>
    <symbol id="i-overview" viewBox="0 0 30 30" fill="none" stroke="currentColor" stroke-width="1.3"><path d="M7 4h12l4 4v18H7z"/><path d="M10 10h8M10 13h10M10 16h6M10 19h5"/><circle cx="20" cy="19" r="3.5"/><path d="M22.5 21.5l3.5 3.5" stroke-width="2"/></symbol>
    <symbol id="i-book" viewBox="0 0 34 32" fill="none" stroke="currentColor" stroke-width="1.6"><path d="M17 8c-4-3-9-3-14-2v20c5-1 10-1 14 2 4-3 9-3 14-2V6c-5-1-10-1-14 2zM17 8v20"/></symbol>
    <symbol id="i-practice" viewBox="0 0 34 32"><g fill="none" stroke="currentColor" stroke-width="1.3"><rect x="5" y="2" width="12" height="14"/><rect x="17" y="2" width="12" height="14"/><rect x="5" y="16" width="12" height="14"/><rect x="17" y="16" width="12" height="14"/></g><g fill="currentColor" font-family="Lato, sans-serif" font-size="11" text-anchor="middle"><text x="11" y="13">a</text><text x="23" y="13">b</text><text x="11" y="27">c</text><text x="23" y="27">d</text></g></symbol>
    <symbol id="i-home" viewBox="0 0 34 32"><path d="M17 1 1 16h5v15h8v-9h6v9h8V16h5z" fill="currentColor"/></symbol>
    <symbol id="i-games" viewBox="0 0 34 32" fill="none" stroke="currentColor" stroke-width="1.5"><path d="M9 9h16c4 0 6 4 7 10s-3 8-6 4l-3-4H11l-3 4c-3 4-7 2-6-4S5 9 9 9z"/><path d="M9 13v6M6 16h6"/><circle cx="23" cy="14" r="1" fill="currentColor"/><circle cx="26" cy="17" r="1" fill="currentColor"/></symbol>
    <symbol id="i-tests" viewBox="0 0 34 32" fill="none" stroke="currentColor" stroke-width="1.4"><path d="M7 4h17v26H7z"/><path d="M10 12h8M10 16h10M10 20h10M10 24h7"/><path d="M20 14 29 3l2 2-9 11-3 1z"/></symbol>
  </defs>
</svg>

<!-- Variant 1: light -->
<section class="screen screen--light" aria-label="Home screen, light theme">
  <header class="app-bar"><svg class="menu-icon"><use href="#i-menu"/></svg><h1>Home</h1></header>
  <div class="greeting"><p class="greeting__hello">welcome back,</p><p class="greeting__name">MAYA</p></div>
  <div class="greeting-rule"></div>
  <div class="score"><span class="score__label">SCORE</span><div class="score__row"><span class="score__value">650</span><svg class="score__arrow"><use href="#i-down"/></svg><span class="score__delta">-18</span></div></div>
  <div class="period-tabs"><span class="is-active">Daily</span><span>Weekly</span></div>
  <div class="stats">
    <svg class="stats__chevron stats__chevron--prev"><use href="#i-prev"/></svg>
    <div class="stats__track">
      <div class="stat"><span class="stat__label">Completion</span><span class="stat__value">84%<svg class="stat__up"><use href="#i-up"/></svg>+4</span></div>
      <div class="stat"><span class="stat__label">Sessions</span><span class="stat__value">20<svg class="stat__up"><use href="#i-up"/></svg>+3</span></div>
      <div class="stat"><span class="stat__label">Min.</span><span class="stat__value">18<svg class="stat__up"><use href="#i-up"/></svg>+10</span></div>
    </div>
    <svg class="stats__chevron stats__chevron--next"><use href="#i-next"/></svg>
  </div>
  <div class="section-rule"></div>
  <ul class="shortcuts">
    <li class="shortcut shortcut--active"><div class="shortcut__circle"><svg><use href="#i-chart"/></svg></div>Analytics</li>
    <li class="shortcut"><div class="shortcut__circle"><svg><use href="#i-overview"/></svg></div>Course Overview</li>
    <li class="shortcut"><div class="shortcut__circle">33</div>Days until test</li>
  </ul>
  <p class="up-next"><span class="up-next__label">Up Next:</span> Sentence Correction<br>Lesson 4</p>
  <nav class="tab-bar">
    <span class="tab-bar__item"><svg><use href="#i-book"/></svg>Theory</span>
    <span class="tab-bar__item"><svg><use href="#i-practice"/></svg>Practice</span>
    <span class="tab-bar__item is-active"><svg><use href="#i-home"/></svg>Home</span>
    <span class="tab-bar__item"><svg><use href="#i-games"/></svg>Games</span>
    <span class="tab-bar__item"><svg><use href="#i-tests"/></svg>Tests</span>
  </nav>
</section>

<!-- Variant 2: blue -->
<section class="screen screen--blue" aria-label="Home screen, blue theme">
  <header class="app-bar"><svg class="menu-icon"><use href="#i-menu"/></svg><h1>Home</h1></header>
  <div class="greeting"><p class="greeting__hello">Welcome back,</p><p class="greeting__name">MAYA</p></div>
  <div class="score"><span class="score__label">SCORE</span><div class="score__row"><span class="score__value">650</span><svg class="score__arrow"><use href="#i-down"/></svg><span class="score__delta">-18</span></div></div>
  <div class="period-tabs"><span class="is-active">Daily</span><span>Weekly</span></div>
  <div class="stats">
    <svg class="stats__chevron stats__chevron--prev"><use href="#i-prev"/></svg>
    <div class="stats__track">
      <div class="stat"><span class="stat__label">Completion</span><span class="stat__value">84%<svg class="stat__up"><use href="#i-up"/></svg>+4</span></div>
      <div class="stat"><span class="stat__label">Sessions</span><span class="stat__value">20<svg class="stat__up"><use href="#i-up"/></svg>+3</span></div>
      <div class="stat"><span class="stat__label">Min.</span><span class="stat__value">18<svg class="stat__up"><use href="#i-up"/></svg>+10</span></div>
    </div>
    <svg class="stats__chevron stats__chevron--next"><use href="#i-next"/></svg>
  </div>
  <div class="section-rule"></div>
  <ul class="shortcuts">
    <li class="shortcut shortcut--active"><div class="shortcut__circle"><svg><use href="#i-chart"/></svg></div>Analytics</li>
    <li class="shortcut"><div class="shortcut__circle"><svg><use href="#i-overview"/></svg></div>Course Overview</li>
    <li class="shortcut"><div class="shortcut__circle">33</div>Days until test</li>
  </ul>
  <p class="up-next"><span class="up-next__label">Up Next:</span> Sentence Correction<br>Lesson 4</p>
  <nav class="tab-bar">
    <span class="tab-bar__item"><svg><use href="#i-book"/></svg>Theory</span>
    <span class="tab-bar__item"><svg><use href="#i-practice"/></svg>Practice</span>
    <span class="tab-bar__item is-active"><svg><use href="#i-home"/></svg>Home</span>
    <span class="tab-bar__item"><svg><use href="#i-games"/></svg>Games</span>
    <span class="tab-bar__item"><svg><use href="#i-tests"/></svg>Tests</span>
  </nav>
</section>

<!-- Variant 3: dark -->
<section class="screen screen--dark" aria-label="Home screen, dark theme">
  <header class="app-bar"><svg class="menu-icon"><use href="#i-menu"/></svg><h1>Home</h1></header>
  <div class="greeting-band"></div>
  <div class="greeting"><p class="greeting__hello">welcome back,</p><p class="greeting__name">MAYA</p></div>
  <div class="score"><span class="score__label">SCORE</span><div class="score__row"><span class="score__value">650</span><svg class="score__arrow"><use href="#i-down"/></svg><span class="score__delta">-18</span></div></div>
  <div class="period-tabs"><span class="is-active">Daily</span><span>Weekly</span></div>
  <div class="stats">
    <svg class="stats__chevron stats__chevron--prev"><use href="#i-prev"/></svg>
    <div class="stats__track">
      <div class="stat"><span class="stat__label">Completion</span><span class="stat__value">84%<svg class="stat__up"><use href="#i-up"/></svg>+4</span></div>
      <div class="stat"><span class="stat__label">Sessions</span><span class="stat__value">20<svg class="stat__up"><use href="#i-up"/></svg>+3</span></div>
      <div class="stat"><span class="stat__label">Min.</span><span class="stat__value">18<svg class="stat__up"><use href="#i-up"/></svg>+10</span></div>
    </div>
    <svg class="stats__chevron stats__chevron--next"><use href="#i-next"/></svg>
  </div>
  <div class="section-rule"></div>
  <ul class="shortcuts">
    <li class="shortcut shortcut--active"><div class="shortcut__circle"><svg><use href="#i-chart"/></svg></div>Analytics</li>
    <li class="shortcut"><div class="shortcut__circle"><svg><use href="#i-overview"/></svg></div>Course Overview</li>
    <li class="shortcut"><div class="shortcut__circle">33</div>Days until test</li>
  </ul>
  <p class="up-next"><span class="up-next__label">Up Next:</span> Sentence Correction<br>Lesson 4</p>
  <nav class="tab-bar">
    <span class="tab-bar__item"><svg><use href="#i-book"/></svg>Theory</span>
    <span class="tab-bar__item"><svg><use href="#i-practice"/></svg>Practice</span>
    <span class="tab-bar__item is-active"><svg><use href="#i-home"/></svg>Home</span>
    <span class="tab-bar__item"><svg><use href="#i-games"/></svg>Games</span>
    <span class="tab-bar__item"><svg><use href="#i-tests"/></svg>Tests</span>
  </nav>
</section>

</body>
</html>
```